Massage-Creme label for a young pharmacy

We are a young pharmacy which is part of a big union. We developed for a customer a very good massage creme with aloe vera, coconut oil, and many more advantages and as well a massage jelly. All we need is a good and affordable label which is beatiful and helps us to promote our product. As we want to develop further products, it would be very cool to have a corporate label for all upcoming products.

Target Market(s)

professional masseurs and physiotherapists

Industry/Entity Type

Health And Wellness

Font styles to use
Sans Serif
Decorative

Colors

Designer to choose colors to be used in the design.

Requirements
Must have
• Professionally looking design (but I'm sure you are doing so... :-)
Nice to have
• Label can have any shape. What you see is just a bad label with corresponding sizes, so you can imagine how it would look like in the final state.
Should not have
• If possible, the label should not be completely black (although it might look cool) as we are printing it on our own Vestrel kp812-tx and black is difficult to print (and very costy).

```html
<!DOCTYPE html>
<html lang="de">
<head>
<meta charset="utf-8">
<title>Massage-Crème Etikett</title>
<link href="https://fonts.googleapis.com/css2?family=Arimo:wght@400;700&family=Mr+Dafoe&display=swap" rel="stylesheet">
<style>
  :root {
    --backdrop: #efeef3;
    --lime: #bccd5c;
    --leaf: #7ea84c;
    --forest: #2f7c4f;
    --ink: #1d2a14;
    --ink-soft: #3b5a2c;
    --badge-red: #d8231f;
    --white: #ffffff;
    --brand: #6b4a72;
  }
  * { box-sizing: border-box; margin: 0; padding: 0; }
  html, body { width: 1200px; height: 900px; overflow: hidden; background: var(--backdrop); }
  body { font-family: "Arimo", Arial, sans-serif; color: var(--ink); }

  .label {
    position: absolute; left: 60px; top: 10px; width: 1080px; height: 880px;
    background: linear-gradient(180deg, var(--lime) 0%, var(--leaf) 50%, var(--forest) 100%);
  }

  .product-title {
    position: absolute; left: 100px; top: 118px; width: 380px;
    font-family: "Mr Dafoe", cursive; font-size: 74px; line-height: 1; color: var(--ink);
    transform: rotate(-4deg); text-align: center;
  }
  .variant {
    position: absolute; left: 105px; top: 268px; width: 350px;
    display: flex; align-items: center; gap: 14px;
    font-size: 14px; letter-spacing: 0.5px; color: var(--ink);
  }
  .variant::before, .variant::after { content: ""; flex: 1; height: 2px; background: var(--ink); }

  .badge { position: absolute; left: 62px; top: 300px; width: 150px; height: 92px; }
  .badge-text {
    position: absolute; left: 62px; top: 326px; width: 150px;
    text-align: center; font-size: 15px; line-height: 1.15; color: var(--ink);
  }

  .ingredients-visual {
    position: absolute; left: 80px; top: 470px; width: 390px; height: 352px;
    border-radius: 40% 40% 30% 30%;
    background: radial-gradient(ellipse at 60% 45%, #c9a56a 0%, #8fc56a 35%, #4fa652 70%, rgba(79,166,82,0) 100%);
  }

  .info {
    position: absolute; left: 612px; top: 138px; width: 390px;
    text-align: center; font-size: 14px; line-height: 1.2; color: var(--ink);
  }
  .info p { margin-bottom: 18px; }
  .ph { display: inline-block; padding: 0 16px 10px; border-bottom: 2px solid var(--ink); position: relative; margin-bottom: 22px; }
  .ph::after { content: ""; position: absolute; left: 50%; bottom: -4px; width: 6px; height: 6px; margin-left: -3px; border-radius: 50%; background: var(--ink); }
  .info .note { font-size: 11px; margin-bottom: 16px; }
  .free-of {
    margin: 0 auto; width: 320px; border: 2px solid var(--ink);
    padding: 8px 10px; font-size: 11px; line-height: 1.2;
  }

  .brand { position: absolute; left: 760px; top: 676px; display: flex; align-items: center; gap: 6px; }
  .brand-mark { width: 10px; height: 10px; background: var(--brand); }
  .brand-name { font-size: 11px; font-weight: 700; color: var(--brand); }
  .brand-claim { position: absolute; left: 776px; top: 692px; font-size: 7px; color: var(--ink-soft); }

  .batch { position: absolute; left: 625px; top: 726px; font-size: 9px; line-height: 1.2; }
  .inci { position: absolute; left: 625px; top: 760px; width: 370px; font-size: 8px; line-height: 1.3; color: var(--ink-soft); }
  .volume { position: absolute; left: 755px; top: 826px; font-size: 16px; color: var(--ink-soft); }
</style>
</head>
<body>
  <main class="label">
    <h1 class="product-title">Massage-Crème</h1>
    <div class="variant">COCONUT - ALOE VERA</div>

    <svg class="badge" viewBox="0 0 150 92" aria-hidden="true">
      <polygon fill="var(--badge-red)" points="75,0 86,8 100,3 107,13 122,12 124,23 139,27 135,38 148,46 135,54 139,65 124,69 122,80 107,79 100,89 86,84 75,92 64,84 50,89 43,79 28,80 26,69 11,65 15,54 2,46 15,38 11,27 26,23 28,12 43,13 50,3 64,8"/>
      <ellipse cx="75" cy="46" rx="58" ry="32" fill="var(--white)"/>
    </svg>
    <div class="badge-text">energetisch<br>leitend !</div>

    <div class="ingredients-visual" role="img" aria-label="Aloe-Vera-Blätter, aufgebrochene Kokosnuss und Ölfläschchen"></div>

    <section class="info">
      <p>Hochwertige und sehr hautschonende Emulsion mit hervorragendem Gleitverhalten für die professionelle Massage.</p>
      <p>Hilft durch den hohen Gehalt an Aloe Vera-Gel (50%), die Feuchtigkeit der Haut zu erhalten und schützt durch die Zugabe von Panthenol (= Provitamin B5) und Allantoin vor Hautreizungen.</p>
      <p>Speziell für die (bio-)energetische Massage entwickelt.</p>
      <div class="ph">pH-neutral für die Haut (pH-Wert = 5.5)</div>
      <p class="note">Bei der Entwicklung unserer Produkte legen wir grossen Wert auf gute Verträglichkeit und hochwertige Rohstoffe.</p>
      <div class="free-of">Dieses Produkt ist frei von Parabenen, Mineralölen (Paraffin/Vaseline), Silikonen, Farbstoffen und Mikroplastik (Acrylate).</div>
    </section>

    <div class="brand"><span class="brand-mark"></span><span class="brand-name">Apotheke Lindenhof</span></div>
    <div class="brand-claim">Ihre Gesundheit</div>

    <div class="batch">Exp: 03/2021<br>Lot: 913015/A</div>
    <p class="inci">Ingredients: aqua, glycerin, aloe barbadensis leaf juice, cocos nucifera oil, cetearyl alcohol, panthenol, allantoin, caprylic triglyceride, tocopherol, xanthan gum, sodium benzoate, potassium sorbate, citric acid, parfum.</p>
    <div class="volume">℮ 1000 ml</div>
  </main>
</body>
</html>
```